Online business manager needs a website

I need a website designed and then coded. I am an online business manager serving a number of different industries providing administrative support to existing small businesses and helping solo practitioners get their new business up and running.

I didn't have a logo formally designed but have been using the attached avatar and wouldn't mind something that incorporated that.

The business doesn't have an official name, so I've just been using my name Lena Morvath, Online Business Manager or Lena Morvath, OBM. I've attached two documents that I have made previously for an example of content.

I would prefer the final site be in Wordpress.

Requirements
Must have
• A way to contact me, testimonials, list of services

```html
<!DOCTYPE html>
<html lang="en">
<head>
<meta charset="utf-8">
<title>Lena Morvath — Online Business Manager</title>
<link rel="stylesheet" href="https://fonts.googleapis.com/css2?family=Noto+Sans:wght@400;500;600;700&family=Lato:wght@400;700&display=swap">
<style>
:root{
  --purple:#4b1c80;
  --purple-deep:#3c1268;
  --purple-band:#55238f;
  --lilac:#b79ad6;
  --ink:#1b1b1f;
  --body:#3a3a42;
  --card:#f5f4f8;
  --white:#ffffff;
  --black:#000000;
}
*{box-sizing:border-box;margin:0;padding:0}
html,body{width:1200px;height:3767px;overflow:hidden;background:var(--white)}
body{position:relative;font-family:"Lato",sans-serif;color:var(--body)}
.abs{position:absolute}
h1,h2,h3,.brand,.btn,.nav a{font-family:"Noto Sans",sans-serif}
.btn{display:inline-flex;align-items:center;gap:9px;height:50px;padding:0 18px;border-radius:25px;background:var(--purple);color:var(--white);font-size:16px;font-weight:700;box-shadow:0 4px 10px rgba(40,10,80,.3)}
.btn.light{background:var(--white);color:var(--purple)}
.arrow{width:14px;height:14px;border-radius:50%;background:currentColor;position:relative}
.arrow::after{content:"";position:absolute;left:3px;top:4px;border-left:6px solid var(--purple);border-top:3px solid transparent;border-bottom:3px solid transparent}
.btn:not(.light) .arrow::after{border-left-color:var(--purple)}
.btn .arrow{background:var(--white)}
.btn.light .arrow{background:var(--purple)}
.btn.light .arrow::after{border-left-color:var(--white)}

/* header */
.topline{left:0;top:0;width:1200px;height:5px;background:var(--purple)}
.brand{left:110px;top:8px;font-size:32px;font-weight:500;color:var(--purple-deep)}
.tagline{left:98px;top:51px;font-size:15px;color:var(--ink);font-family:"Noto Sans",sans-serif}
.nav{left:572px;top:32px;display:flex;gap:36px;font-size:16px}
.nav a{color:var(--ink);text-decoration:none}
.nav a.active{color:var(--purple);font-weight:500}
.header-cta{left:968px;top:18px}

/* hero */
.hero{left:0;top:85px;width:1200px;height:599px;background:linear-gradient(105deg,#5f99ad 0%,#2f7591 35%,#144e6b 70%,#3a6f87 100%)}
.hero h1{left:98px;top:170px;font-size:56px;line-height:56px;font-weight:700;color:var(--white)}
.hero p{left:98px;top:290px;width:380px;font-size:15px;line-height:34px;color:var(--white)}
.hero .btn{left:97px;top:372px}

/* about */
.about-back{left:98px;top:838px;width:390px;height:397px;background:var(--purple)}
.about-frame{left:138px;top:783px;width:403px;height:410px;border:5px solid var(--lilac);border-radius:6px;background:var(--white)}
.about-photo{left:124px;top:811px;width:390px;height:397px;background:linear-gradient(135deg,#b13f7b,#d45a93 45%,#6e3e4a 100%);border-radius:4px}
.about h2{left:585px;top:823px;font-size:33px;font-weight:600;color:var(--ink)}
.about h2 span,.section-title span{color:var(--purple)}
.about p{left:585px;top:877px;width:520px;font-size:15px;line-height:31px}
.about .btn{left:585px;top:1140px}

/* band */
.band{left:0;top:1320px;width:1200px;height:295px;background:linear-gradient(90deg,#4d1d85,#5a2597 50%,#4a1a80)}
.band h2{left:0;top:1368px;width:1200px;text-align:center;font-size:33px;font-weight:600;color:var(--white)}
.band p{left:180px;top:1422px;width:840px;text-align:center;font-size:15px;line-height:34px;color:var(--white)}
.band .btn{left:519px;top:1505px}

/* what I do best */
.section-title{left:0;width:1200px;text-align:center;font-size:33px;font-weight:600;color:var(--ink)}
.skill{top:1744px;width:224px;height:168px;background:var(--card);border-radius:4px;box-shadow:0 6px 14px rgba(0,0,0,.1);text-align:center}
.skill svg{margin-top:32px}
.skill h3{font-size:17px;font-weight:600;color:var(--ink);margin-top:10px}
.chev{top:1818px;font-size:20px;color:var(--ink)}

/* services */
.svc-band{left:0;top:2229px;width:1200px;height:278px;background:var(--purple-band)}
.svc{top:2075px;width:318px;height:366px;background:var(--white);border-radius:5px;overflow:hidden;text-align:center;box-shadow:0 4px 12px rgba(0,0,0,.08)}
.svc .pic{height:200px}
.svc h3{font-size:19px;font-weight:600;color:var(--ink);margin-top:38px}
.svc p{width:250px;margin:6px auto 0;font-size:14.5px;line-height:31px}
.sq-arrow{width:18px;height:18px;border:1.5px solid currentColor;border-radius:5px;display:flex;align-items:center;justify-content:center;font-size:12px;line-height:1}

/* testimonials */
.t-shadow{left:105px;top:2597px;width:380px;height:360px;background:#ece8f2;border-radius:4px}
.t-photo{left:99px;top:2590px;width:376px;height:358px;background:linear-gradient(140deg,#7e9a4e,#b8a886 45%,#6b4a3d 100%);border-radius:3px}
.testi h2{left:517px;top:2623px;font-size:33px;font-weight:600;color:var(--ink)}
.testi p{left:517px;top:2677px;width:580px;font-size:15px;line-height:31px}
.testi .who{left:517px;top:2810px;font-size:15px;color:var(--ink)}

/* contact */
.footer{left:0;top:3327px;width:1200px;height:440px;background:var(--black)}
.contact{left:98px;top:3028px;width:1003px;height:391px;background:var(--purple-band);border-radius:4px}
.contact h2{left:0;top:3070px;width:1200px;text-align:center;font-size:33px;font-weight:600;color:var(--white)}
.field{border:1px solid rgba(255,255,255,.75);color:var(--white);font-size:15px;padding:14px 21px}
.contact-btn{left:526px;top:3291px;height:50px}

/* footer text */
.f-brand{left:0;top:3466px;width:1200px;text-align:center;font-family:"Noto Sans",sans-serif;font-size:32px;font-weight:600;color:var(--white)}
.f-tag{left:0;top:3518px;width:1200px;text-align:center;font-family:"Noto Sans",sans-serif;font-size:16px;color:var(--white)}
.f-nav{left:318px;top:3570px;display:flex;gap:56px;font-family:"Noto Sans",sans-serif;font-size:15px;color:var(--white)}
.f-item{top:3622px;display:flex;align-items:center;gap:14px;color:var(--white);font-size:15px}
.f-icon{width:40px;height:34px;background:var(--purple);border-radius:3px;display:flex;align-items:center;justify-content:center}
.copy{left:0;top:3700px;width:1200px;text-align:center;font-size:14.5px;color:var(--white)}
</style>
</head>
<body>

<header>
  <div class="abs topline"></div>
  <div class="abs brand">Lena Morvath</div>
  <div class="abs tagline">Online Business Manager</div>
  <nav class="abs nav"><a class="active">Home</a><a>About Us</a><a>Services</a><a>Testimonials</a></nav>
  <div class="abs btn header-cta">Contact Us <span class="arrow"></span></div>
</header>

<section class="hero-wrap">
  <div class="abs hero" role="img" aria-label="Businessman pointing a pen at glowing financial charts and figures"></div>
  <h1 class="abs hero" style="background:none;height:auto;width:500px;left:98px;top:255px">Welcome To<br>Lena Morvath</h1>
  <p class="abs" style="left:96px;top:372px;width:380px;font-size:15px;line-height:34px;color:#fff">I thrive while working independently, which means you can be confident when leaving tasks for me.</p>
  <div class="abs btn" style="left:97px;top:457px">Get Started <span class="arrow"></span></div>
</section>

<section class="about">
  <div class="abs about-back"></div>
  <div class="abs about-frame"></div>
  <div class="abs about-photo" role="img" aria-label="Portrait photo of Lena in front of pink flowering shrubs"></div>
  <h2 class="abs"><span>About</span> Me</h2>
  <p class="abs">Hi! I'm so excited that you have chosen to explore my portfolio. Helping businesses achieve their goals is my passion, and I'm thrilled that with my assistance you will have more time for your own passion project. I thrive while working independently, which means you can be confident when leaving tasks for me. The type of work that lights me up is anything involving organization and/or spreadsheets. You need data analyzed that includes multiple nested if formulas? You have an overwhelming amount of email to sort through and appointments to book? I'm your gal!</p>
  <div class="abs btn">Read More <span class="arrow"></span></div>
</section>

<section>
  <div class="abs band" role="img" aria-label="Purple-tinted photo of a desk with paperwork and a keyboard"></div>
  <h2 class="abs" style="left:0;top:1368px;width:1200px;text-align:center;font-size:33px;font-weight:600;color:#fff">Digital Business Manager</h2>
  <p class="abs" style="left:180px;top:1422px;width:840px;text-align:center;font-size:15px;line-height:34px;color:#fff">focused on the live event and entertainment industry. Helping artists and owners to better manage their career and business by strategically reviewing systems, recommending operational efficiencies, and managing inboxes.</p>
  <div class="abs btn light" style="left:519px;top:1505px">Let's Connect <span class="arrow"></span></div>
</section>

<section>
  <h2 class="abs section-title" style="top:1670px"><span>What I</span> Do Best</h2>
  <div class="abs chev" style="left:66px">&#8249;</div>
  <div class="abs chev" style="left:1128px">&#8250;</div>
  <div class="abs skill" style="left:98px">
    <svg width="60" height="58" viewBox="0 0 60 58" fill="none" stroke="#222" stroke-width="2"><rect x="14" y="3" width="30" height="40" rx="2"/><path d="M20 14h18M20 21h18M20 28h12" stroke="#4b1c80"/><rect x="4" y="36" width="52" height="18" rx="2"/></svg>
    <h3>Data Entry</h3>
  </div>
  <div class="abs skill" style="left:360px">
    <svg width="64" height="58" viewBox="0 0 64 58" fill="none" stroke="#4b1c80" stroke-width="2"><rect x="4" y="18" width="56" height="36" rx="2"/><path d="M4 20l28 20 28-20"/><circle cx="32" cy="14" r="9" stroke="#222"/><circle cx="32" cy="14" r="3" stroke="#222"/></svg>
    <h3>Email Management</h3>
  </div>
  <div class="abs skill" style="left:620px">
    <svg width="64" height="58" viewBox="0 0 64 58" fill="none" stroke="#222" stroke-width="2"><rect x="3" y="4" width="50" height="44" rx="2"/><path d="M3 12h50M10 40v-6M17 40v-10M24 40v-8" /><rect x="36" y="26" width="24" height="28" rx="2" stroke="#4b1c80"/><circle cx="48" cy="40" r="7" stroke="#4b1c80"/></svg>
    <h3>Financial Analytics</h3>
  </div>
  <div class="abs skill" style="left:878px">
    <svg width="64" height="60" viewBox="0 0 64 60" fill="none" stroke="#222" stroke-width="2"><circle cx="38" cy="20" r="12"/><circle cx="38" cy="20" r="5"/><path d="M4 48c8-8 16-8 22-4h14c3 0 3 5 0 5H26" stroke="#4b1c80"/><path d="M26 49l18-2 14-10" stroke="#4b1c80"/></svg>
    <h3>Project Management</h3>
  </div>
</section>

<section>
  <h2 class="abs section-title" style="top:1989px"><span>Our</span> Services</h2>
  <div class="abs svc-band"></div>
  <div class="abs sq-arrow" style="left:49px;top:2346px;color:#d9c9ee">&#8594;</div>
  <div class="abs sq-arrow" style="left:1132px;top:2346px;color:#fff">&#8592;</div>
  <div class="abs svc" style="left:98px">
    <div class="pic" role="img" aria-label="Hands typing on a laptop with glowing digital overlay" style="background:linear-gradient(135deg,#b9c4c8,#4e6a72 60%,#1f2a2e)"></div>
    <h3>Virtual Assistance</h3>
    <p>Calendar Management Email Management Light Graphic Design Data Entry</p>
  </div>
  <div class="abs svc" style="left:441px">
    <div class="pic" role="img" aria-label="Colleagues smiling during a meeting at a table" style="background:linear-gradient(135deg,#9c8a78,#d6c2a9 45%,#2c3b57)"></div>
    <h3>Finance Management</h3>
    <p>Create Invoices Track Receivables Analyze Expenses Year Over Year Analytics</p>
  </div>
  <div class="abs svc" style="left:783px">
    <div class="pic" role="img" aria-label="Hands on a laptop with floating digital folders" style="background:linear-gradient(135deg,#3a3f52,#6b6f86 50%,#b6a69a)"></div>
    <h3>Business Management</h3>
    <p>Creation of Operating Procedures Review of Website Strategy Reporting and Analytics Project Management</p>
  </div>
</section>

<section class="testi">
  <div class="abs t-shadow"></div>
  <div class="abs t-photo" role="img" aria-label="Portrait photo of a smiling client outdoors"></div>
  <h2 class="abs">Testimonials</h2>
  <p class="abs">When it became apparent that a project would take more time than I had, Lena stepped up to take on the required research. She was thorough and timely; able to meet a last-minute 12-hour deadline. I would highly recommend Lena to assist with your next project.</p>
  <div class="abs who">Dana R. Owner, Bluecrest Renovations</div>
  <div class="abs sq-arrow" style="left:518px;top:2853px;color:#aaa">&#8594;</div>
  <div class="abs sq-arrow" style="left:554px;top:2853px;color:#111">&#8592;</div>
</section>

<section>
  <div class="abs footer"></div>
  <div class="abs contact"></div>
  <h2 class="abs" style="left:0;top:3070px;width:1200px;text-align:center;font-size:33px;font-weight:600;color:#fff">Contact Us</h2>
  <div class="abs field" style="left:157px;top:3135px;width:430px;height:48px">Enter Name</div>
  <div class="abs field" style="left:611px;top:3135px;width:431px;height:48px">Enter Email</div>
  <div class="abs field" style="left:157px;top:3211px;width:886px;height:80px">Message</div>
  <div class="abs btn light" style="left:526px;top:3291px">Submit <span class="arrow"></span></div>
</section>

<footer>
  <div class="abs f-brand">Lena Morvath</div>
  <div class="abs f-tag">Online Business Manager</div>
  <div class="abs f-nav"><span>Home</span><span>About Us</span><span>Services</span><span>Testimonials</span><span>Contact Us</span></div>
  <div class="abs f-item" style="left:217px">
    <span class="f-icon"><svg width="16" height="16" viewBox="0 0 24 24" fill="#fff"><path d="M6.6 10.8a15 15 0 006.6 6.6l2.2-2.2a1 1 0 011-.25 11.4 11.4 0 003.6.57 1 1 0 011 1V20a1 1 0 01-1 1A17 17 0 013 4a1 1 0 011-1h3.5a1 1 0 011 1c0 1.25.2 2.45.57 3.57a1 1 0 01-.25 1z"/></svg></span>555.014.2298
  </div>
  <div class="abs f-item" style="left:482px">
    <span class="f-icon"><svg width="16" height="13" viewBox="0 0 16 13" fill="#fff"><path d="M0 0h16v2L8 7 0 2z"/><path d="M0 4l8 5 8-5v9H0z"/></svg></span>lena.morvath@example.com
  </div>
  <div class="abs f-item" style="left:826px">
    <span class="f-icon"><span style="width:12px;height:12px;background:#fff;display:block"></span></span>Lena Ann Morvath
  </div>
  <div class="abs copy">Copyrights@2023.Lena Morvath Online Business Manager.All Rights Reserved</div>
</footer>

</body>
</html>
```